New Business Card Design Project LORVANTI-Italy

we are LORVANTI-Italy
our company in the market for 3 years we are luxury cosmetic company and its about time for a facelift :)
i will like to have elegant luxurious and unique business card
that will give the person that get it a unique, luxurious and elegant impression
I'm VERY OPEN FOR NEW IDEAS , even duo i add a few files of things that i see on line and i like them

i add my logo as well
my website is LORVANTI.COM
(if you would like to see the main style that we have)

Target Market(s)

adult that have money :)

Industry/Entity Type

Business

Contact Information for Business Card

Name - Dario Lorvanti
Position - CEO and CO Founder
address - 4817 E Halvern
telephone - 555-384-1926
email - dario@lorvanti.com
fax - 555-384-1926
website - LORVANTI.COM

Colors
000000
959595
fbee3e
ffffff

Requirements
Must have
• big logo in GOLD color
• elegant look
• impressive
Nice to have
• not must but maybe classy pattern background
• not must but maybe emblem
• maybe clear plastic business card
Should not have
• colors
• images

```html
<!DOCTYPE html>
<html lang="en">
<head>
<meta charset="utf-8">
<title>LORVANTI-Italy Business Card</title>
<link rel="stylesheet" href="https://fonts.googleapis.com/css2?family=Marcellus+SC&family=PT+Sans:wght@400;700&display=swap">
<style>
  :root {
    --backdrop: #4a403b;
    --card: #111111;
    --card-edge: #1c1c1c;
    --gold: #d4a63a;
    --grey: #959595;
    --white: #ffffff;
  }
  * { margin: 0; padding: 0; box-sizing: border-box; }
  html, body {
    width: 1200px;
    height: 864px;
    overflow: hidden;
    background: var(--backdrop);
  }
  .canvas {
    position: relative;
    width: 1200px;
    height: 864px;
  }
  .card {
    position: absolute;
    width: 520px;
    height: 300px;
    background: var(--card);
    border: 1px solid var(--card-edge);
    box-shadow: 0 10px 24px rgba(0, 0, 0, 0.45);
  }
  .card-front { left: 50px; top: 130px; }
  .card-back { left: 630px; top: 430px; }

  /* Front */
  .brand {
    position: absolute;
    left: 0;
    right: 0;
    top: 62px;
    display: flex;
    flex-direction: column;
    align-items: center;
  }
  .brand-mark {
    width: 64px;
    height: 64px;
  }
  .brand-name {
    margin-top: 18px;
    font-family: "Marcellus SC", serif;
    font-size: 38px;
    letter-spacing: 2px;
    color: var(--gold);
  }
  .front-web {
    position: absolute;
    left: 0;
    right: 0;
    bottom: 40px;
    text-align: center;
    font-family: "PT Sans", sans-serif;
    font-size: 15px;
    letter-spacing: 4px;
    color: var(--grey);
  }

  /* Back */
  .person {
    position: absolute;
    right: 26px;
    top: 96px;
    text-align: right;
  }
  .person-name {
    font-family: "Marcellus SC", serif;
    font-size: 22px;
    letter-spacing: 1px;
    color: var(--gold);
  }
  .person-title {
    font-family: "PT Sans", sans-serif;
    font-size: 15px;
    color: var(--white);
    margin-top: 2px;
  }
  .contact {
    position: absolute;
    left: 26px;
    bottom: 34px;
    font-family: "PT Sans", sans-serif;
    font-size: 13px;
    line-height: 1.5;
    color: var(--white);
  }
  .contact-label {
    font-weight: 700;
    color: var(--gold);
  }
</style>
</head>
<body>
<main class="canvas">
  <section class="card card-front" aria-label="Card front">
    <div class="brand">
      <svg class="brand-mark" viewBox="0 0 64 64" aria-hidden="true">
        <circle cx="32" cy="32" r="30" fill="none" stroke="var(--gold)" stroke-width="2"/>
      </svg>
      <div class="brand-name">LORVANTI Italy</div>
    </div>
    <div class="front-web">www.lorvanti.com</div>
  </section>

  <section class="card card-back" aria-label="Card back">
    <div class="person">
      <div class="person-name">Dario Lorvanti</div>
      <div class="person-title">CEO &amp; CO Founder</div>
    </div>
    <div class="contact">
      <div>4817 E Halvern</div>
      <div><span class="contact-label">PHONE :</span> 555-384-1926 <span class="contact-label">FAX :</span> 555-384-1926</div>
      <div><span class="contact-label">EMAIL :</span> dario@lorvanti.com <span class="contact-label">WEB :</span> LORVANTI.COM</div>
    </div>
  </section>
</main>
</body>
</html>
```